Upscale business cards needed for Board of Directors

We need professional business cards created for members of our family business Board of Directors. We would like these relatively simple and straightforward, but also with a unique element to set them apart. Probably stick with neutral and simple colors - white, grey etc. We need space for the traditional elements, including name, title, address, email/phone number. And we will be creating several from this template so it needs to be template that is easy to switch information in and out of.
Business
See description

```html
<!DOCTYPE html>
<html lang="en">
<head>
<meta charset="UTF-8">
<title>Corvell Holdings – Business Cards</title>
<link href="https://fonts.googleapis.com/css2?family=Saira+Semi+Condensed:wght@700&family=Roboto:wght@400;500&display=swap" rel="stylesheet">
<style>
  :root {
    --stage-dark: #1a1a1a;
    --stage-light: #6b6b6b;
    --card-dark: #1f1c1b;
    --card-white: #ffffff;
    --gold: #b5a27c;
    --text-light: #f2f0ec;
    --text-muted: #bdbab5;
    --ink: #1f1c1b;
  }
  * { margin: 0; padding: 0; box-sizing: border-box; }
  html, body { width: 1200px; height: 950px; overflow: hidden; }
  body {
    background: radial-gradient(ellipse at 50% 45%, var(--stage-light) 0%, var(--stage-dark) 75%);
    font-family: "Roboto", Arial, sans-serif;
    position: relative;
  }
  .card {
    position: absolute;
    width: 630px;
    height: 360px;
    box-shadow: 0 18px 40px rgba(0,0,0,0.55);
    overflow: hidden;
  }
  .brand-name {
    font-family: "Saira Semi Condensed", "Arial Narrow", sans-serif;
    font-weight: 700;
    text-transform: uppercase;
    line-height: 1;
    white-space: nowrap;
  }
  .brand-name .brand-line-main { display: block; font-size: 60px; letter-spacing: 1px; }
  .brand-name .brand-line-sub { display: block; font-size: 22px; letter-spacing: 10px; margin-top: 4px; }

  /* Front card */
  .card-front {
    left: 110px; top: 70px;
    background: var(--card-dark);
    display: flex; flex-direction: column; align-items: center; justify-content: center;
  }
  .card-front .brand-name { color: var(--text-light); text-align: center; }
  .card-front .front-website {
    margin-top: 50px;
    color: var(--text-muted);
    font-size: 14px;
    letter-spacing: 4px;
  }

  /* Back card */
  .card-back {
    left: 470px; top: 500px;
    background: var(--card-white);
  }
  .accent-bar {
    position: absolute; right: 0; top: 0;
    width: 22px; height: 190px;
    background: var(--gold);
  }
  .contact-panel {
    position: absolute; left: 0; top: 90px;
    width: 300px; height: 270px;
    background: var(--card-dark);
    padding: 34px 30px;
    color: var(--text-light);
  }
  .person-name { color: var(--gold); font-size: 21px; font-weight: 500; }
  .person-title { font-size: 15px; margin-top: 4px; }
  .address { font-size: 14px; line-height: 1.4; margin-top: 20px; color: var(--text-light); }
  .contact-list { list-style: none; margin-top: 14px; }
  .contact-list li {
    display: flex; align-items: center; gap: 10px;
    font-size: 14px; line-height: 1; margin-bottom: 10px;
  }
  .contact-list svg { width: 14px; height: 14px; fill: var(--gold); flex: none; }
  .card-back .brand-name {
    position: absolute; left: 312px; top: 112px;
    width: 280px;
    color: var(--ink); text-align: center;
  }
  .card-back .brand-line-main { font-size: 48px; }
  .card-back .brand-line-sub { font-size: 18px; letter-spacing: 8px; }
</style>
</head>
<body>

<section class="card card-front" aria-label="Business card front">
  <div class="brand-name">
    <span class="brand-line-main">Corvell</span>
    <span class="brand-line-sub">Holdings</span>
  </div>
  <p class="front-website">www.corvellholdings.com</p>
</section>

<section class="card card-back" aria-label="Business card back">
  <div class="accent-bar"></div>
  <div class="contact-panel">
    <p class="person-name">Mark Ellison</p>
    <p class="person-title">President</p>
    <p class="address">2170 Linden Crest Road<br>Lake Haven, NY 11020</p>
    <ul class="contact-list">
      <li>
        <svg viewBox="0 0 16 16" aria-hidden="true"><path d="M3.5 1.5l2.5 0 1 3.5-1.6 1.2a8 8 0 0 0 4.4 4.4L11 9l3.5 1v2.5c0 .8-.7 1.5-1.5 1.5A12 12 0 0 1 2 3c0-.8.7-1.5 1.5-1.5z"/></svg>
        555 0142 7781
      </li>
      <li>
        <svg viewBox="0 0 16 16" aria-hidden="true"><path d="M1 3h14v1.2L8 9 1 4.2z"/><path d="M1 5.6L8 10.4l7-4.8V13H1z"/></svg>
        mark@corvellholdings.com
      </li>
      <li>
        <svg viewBox="0 0 16 16" aria-hidden="true"><circle cx="8" cy="8" r="7"/><path d="M1 8h14M8 1c2.5 2.5 2.5 11.5 0 14M8 1c-2.5 2.5-2.5 11.5 0 14" stroke="#1f1c1b" stroke-width="1" fill="none"/></svg>
        www.corvellholdings.com
      </li>
    </ul>
  </div>
  <div class="brand-name">
    <span class="brand-line-main">Corvell</span>
    <span class="brand-line-sub">Holdings</span>
  </div>
</section>

</body>
</html>
```